Buch-/eBook-Cover zum Thema Magersucht
Zielgruppe
Ich bin Autorin und suche ein passendes Buchcover. Die Zielgruppe für dieses Buch sind Eltern von magersüchtigen Kindern sowie interessierte medizinische und therapeutische Fachkräfte.
Aufgabenstellung
Bei meinem Buch handelt es sich um einen Ratgeber zur Behandlung von Magersucht bei Kindern und Jugendlichen.
Folgendes muss auf die Vorderseite des Buches:
Titel: Teller trägt Trost
Untertitel: Elterngestützte Begleitung im Alltag
Helga Brunsmeier
Ich wünsche mir ein einfühlsames Cover, das die Schwere der Krankheit spiegelt, aber auch die Hoffnung auf Heilung. Bitte keine plumpen Bilder von Waage, Massband oder dünnen Körpern.
Der Klappentext im Word-Dokument ist für die Rückseite des Buchcovers.

```html
<!DOCTYPE html>
<html lang="de">
<head>
<meta charset="utf-8">
<title>Teller trägt Trost – Buchcover</title>
<link href="https://fonts.googleapis.com/css2?family=Lilita+One&family=Roboto+Condensed:wght@700&display=swap" rel="stylesheet">
<style>
  :root {
    --backdrop: #8289cb;
    --sky-teal: #1f5f58;
    --ground-red: #b8443a;
    --bear-cream: #e6dcab;
    --belly-light: #f3eed0;
    --title-red: #e8262e;
    --label-cream: #f1ebc4;
  }
  * { margin: 0; padding: 0; box-sizing: border-box; }
  html, body {
    width: 1200px;
    height: 1200px;
    overflow: hidden;
    background: var(--backdrop);
  }
  .book-cover {
    position: absolute;
    left: 259px;
    top: 118px;
    width: 683px;
    height: 964px;
    overflow: hidden;
  }
  .cover-artwork {
    position: absolute;
    inset: 0;
    background:
      radial-gradient(ellipse 46% 52% at 50% 54%, var(--belly-light) 0%, var(--bear-cream) 55%, rgba(230,220,171,0) 100%),
      linear-gradient(to bottom, var(--sky-teal) 0%, var(--sky-teal) 56%, var(--ground-red) 58%, var(--ground-red) 100%);
  }
  .spine-fold {
    position: absolute;
    left: 28px;
    top: 0;
    bottom: 0;
    width: 2px;
    background: rgba(0,0,0,0.12);
  }
  .cover-title {
    position: absolute;
    left: 0;
    right: 0;
    top: 398px;
    text-align: center;
    font-family: "Lilita One", sans-serif;
    font-size: 70px;
    line-height: 93px;
    letter-spacing: 1px;
    color: var(--title-red);
    text-transform: uppercase;
  }
  .cover-subtitle {
    position: absolute;
    left: 0;
    right: 0;
    top: 664px;
    text-align: center;
    font-family: "Roboto Condensed", sans-serif;
    font-weight: 700;
    font-size: 18px;
    line-height: 23px;
    letter-spacing: 0.5px;
    color: var(--title-red);
  }
  .author-label {
    position: absolute;
    left: 50%;
    top: 882px;
    transform: translateX(-50%);
    padding: 8px 22px 6px;
    background: var(--label-cream);
    font-family: "Lilita One", sans-serif;
    font-size: 25px;
    letter-spacing: 0.5px;
    color: var(--title-red);
    text-transform: uppercase;
    white-space: nowrap;
  }
</style>
</head>
<body>
  <main class="book-cover">
    <div class="cover-artwork" role="img" aria-label="Illustration: großer, rundlicher cremefarbener Bär sitzt auf rotem Boden vor dunkelgrünem Himmel mit blauen Wolken"></div>
    <div class="spine-fold"></div>
    <h1 class="cover-title">Teller<br>trägt<br>Trost</h1>
    <p class="cover-subtitle">Elterngestützte Begleitung<br>im Alltag</p>
    <p class="author-label">Helga Brunsmeier</p>
  </main>
</body>
</html>
```